Destination PDF Template (Editable)

Objective: Create a visually stunning and compelling PDF brochure that showcases The Vorelka Crest Lodge as the ultimate luxury hunting destination in Kyrgyzstan, specializing in Marco Polo and Ibex hunts. The PDF should evoke a sense of exclusivity, adventure, and the breathtaking beauty of the Tian Shan mountains, ultimately driving bookings.
Target Audience: High-net-worth individuals, discerning hunters seeking exceptional experiences, adventure travelers, and those interested in unique and luxurious wilderness experiences.
Overall Tone & Style: Sophisticated, elegant, and aspirational. Think high-end travel magazines combined with a touch of rugged adventure. Avoid anything that feels generic or overly commercial. The design should reflect the unparalleled nature of the lodge and the hunts offered. (I'm attaching a reference PDF that i like), as well as another instructions file. Drive link for photos: https://files.pondery-share.net/box/folders/7KqLm2xVbR4tWz9hN3cJpE6yF0aDs8uG?mode=open
Another Link: https://files.pondery-share.net/box/u/0/folders/9ZtRe4wQmN2bVx7kLp5sHc8jYd3fGa1oU

```html
<!DOCTYPE html>
<html lang="en">
<head>
<meta charset="UTF-8">
<title>A Hunter's Paradise – Where Luxury Roams Free</title>
<link href="https://fonts.googleapis.com/css2?family=Poppins:wght@300;600&family=Source+Sans+3:wght@400&display=swap" rel="stylesheet">
<style>
  :root {
    --page-bg: #f8f8f7;
    --ink: #1f2b3d;
    --body-ink: #2a3446;
    --caption: #ffffff;
  }
  html, body {
    margin: 0;
    padding: 0;
    width: 1200px;
    height: 675px;
    overflow: hidden;
    background: var(--page-bg);
  }
  .spread {
    position: relative;
    width: 1200px;
    height: 675px;
    overflow: hidden;
    background: var(--page-bg);
  }
  .intro {
    position: absolute;
    left: 73px;
    top: 100px;
    width: 451px;
    color: var(--ink);
  }
  .intro-title {
    margin: 0;
    font-family: 'Poppins', sans-serif;
    font-weight: 600;
    font-size: 31px;
    line-height: 1.2;
    letter-spacing: -0.3px;
    padding-left: 2px;
  }
  .intro-subtitle {
    margin: 10px 0 0;
    font-family: 'Poppins', sans-serif;
    font-weight: 300;
    font-size: 31px;
    line-height: 1.2;
    padding-left: 2px;
  }
  .intro-body {
    margin: 40px 0 0;
    font-family: 'Source Sans 3', sans-serif;
    font-size: 17.5px;
    line-height: 31.25px;
    letter-spacing: 0.35px;
    color: var(--body-ink);
    text-align: justify;
  }
  .intro-body + .intro-body {
    margin-top: 31px;
  }
  .gallery {
    position: absolute;
    left: 581px;
    top: 0;
    width: 619px;
    height: 675px;
  }
  .gallery-photo {
    position: absolute;
    left: 0;
    width: 619px;
  }
  .photo-hunter {
    top: 0;
    height: 249px;
    background: linear-gradient(160deg, #c9d6df 0%, #7c8a93 45%, #4a5560 75%, #c7b8a8 100%);
  }
  .photo-valley {
    top: 250px;
    height: 193px;
    background: linear-gradient(180deg, #3d7fc4 0%, #c4d6e6 35%, #9a5a3c 60%, #6f7a55 80%, #8c8c88 100%);
  }
  .photo-lodge {
    top: 444px;
    height: 231px;
    background: linear-gradient(180deg, #5c5f43 0%, #8a7458 35%, #d08a30 60%, #7a5a3a 80%, #4f6d32 100%);
  }
  .valley-caption {
    position: absolute;
    left: 18px;
    top: 131px;
    margin: 0;
    font-family: 'Source Sans 3', sans-serif;
    font-size: 14px;
    letter-spacing: 10.5px;
    color: var(--caption);
    white-space: nowrap;
  }
</style>
</head>
<body>
  <main class="spread">
    <section class="intro">
      <h1 class="intro-title">A Hunter’s Paradise:</h1>
      <h2 class="intro-subtitle">Where Luxury Roams Free</h2>
      <p class="intro-body">Renowned as one of the Best Mountain Hunting Lodges in the World, this Kyrgyzstan camp offers adventure and luxury in the majestic Tian Shan Mountains. Hunt Marco Polo sheep and Ibex across rugged terrain, then relax in unparalleled comfort. Unwind in this secluded oasis, surrounded by breathtaking panoramas of the Kyrgyz landscape.</p>
      <p class="intro-body">This is where the adventure of the hunt seamlessly blends with the comforts of an unparalleled wilderness retreat!</p>
    </section>

    <section class="gallery">
      <div class="gallery-photo photo-hunter" role="img" aria-label="Hunter in camouflage beanie lying prone behind a scoped rifle on a bipod among rocks"></div>
      <div class="gallery-photo photo-valley" role="img" aria-label="Wide mountain valley with red rocky peaks, blue sky, clouds and a braided river">
        <p class="valley-caption">KYRGYZSTAN 2025</p>
      </div>
      <div class="gallery-photo photo-lodge" role="img" aria-label="Long golden timber lodge with brown roof on green grass below mountain slopes"></div>
    </section>
  </main>
</body>
</html>
```